Heron Loan Partners Business Card

We need a business card design for our mortgage servicing company. In addition to servicing the loans of homeowners, we help homeowners with purchasing their homes and any mortgage refinancing. We would like to see designs that use the colors in the logo attached below (gold-ish yellow and navy blue), and any other design you deem fit! The design should communicate a simpler life with smart mortgages provided by Heron.

```html
<!DOCTYPE html>
<html lang="en">
<head>
<meta charset="utf-8">
<title>Heron Loan Partners – Business Card</title>
<link rel="stylesheet" href="https://fonts.googleapis.com/css2?family=Open+Sans:wght@400;600;700&display=swap">
<style>
  :root {
    --stage: #222222;
    --paper: #f4f4f4;
    --gold: #d9aa3c;
    --navy: #262052;
    --ink: #1a1a1a;
    --white: #ffffff;
  }
  * { box-sizing: border-box; margin: 0; padding: 0; }
  html, body {
    width: 1200px; height: 780px; overflow: hidden;
    background: var(--stage);
    font-family: "Open Sans", Arial, sans-serif;
  }
  .canvas {
    position: relative; width: 1200px; height: 780px;
    display: flex; align-items: center; justify-content: center; gap: 40px;
  }
  .card {
    position: relative; width: 540px; height: 309px; overflow: hidden;
    box-shadow: 0 12px 30px rgba(0,0,0,.45);
  }
  .card--front { background: var(--paper); }
  .card--back { background: var(--navy); display: flex; align-items: center; justify-content: center; }

  .front-band { position: absolute; inset: 0; width: 540px; height: 309px; }

  .wordmark {
    font-weight: 700; color: var(--gold); letter-spacing: .5px; white-space: nowrap;
  }
  .card--front .wordmark {
    position: absolute; left: 170px; top: 42px; font-size: 24px;
  }
  .card--back .wordmark { font-size: 40px; }

  .person { position: absolute; left: 34px; top: 112px; }
  .person__name { font-size: 23px; font-weight: 700; line-height: 1.1; }
  .person__first { color: var(--gold); }
  .person__last { color: var(--navy); }
  .person__title { font-size: 11.5px; color: var(--ink); margin-top: 4px; margin-left: 38px; }

  .divider {
    position: absolute; left: 228px; top: 108px; width: 2px; height: 108px; background: var(--ink);
  }

  .contacts { position: absolute; left: 262px; top: 112px; list-style: none; }
  .contacts li {
    display: flex; align-items: center; gap: 10px;
    font-size: 13px; color: var(--ink); height: 22px;
  }
  .contacts svg { width: 13px; height: 13px; flex: none; fill: var(--gold); }

  .address {
    position: absolute; left: 52px; top: 279px;
    font-size: 12.5px; color: var(--white); white-space: nowrap;
  }
</style>
</head>
<body>
<main class="canvas">

  <section class="card card--front" aria-label="Card front">
    <svg class="front-band" viewBox="0 0 540 309" aria-hidden="true">
      <path d="M0,196 C120,272 320,286 540,238 L540,309 L0,309 Z" fill="var(--gold)"/>
      <path d="M62,186 C160,258 330,272 505,232" fill="none" stroke="var(--navy)" stroke-width="3" stroke-linecap="round"/>
    </svg>

    <div class="wordmark">Heron Loan Partners</div>

    <div class="person">
      <p class="person__name"><span class="person__first">Dana</span> <span class="person__last">Whitfield</span></p>
      <p class="person__title">Managing Director</p>
    </div>

    <div class="divider"></div>

    <ul class="contacts">
      <li>
        <svg viewBox="0 0 16 16"><path d="M3.5 1 6 1.6 7 5 5.2 6.2c.8 1.8 2.2 3.2 4.6 4.6L11 9l3.4 1 .6 2.5-2 2C7 14 2 9 1.5 3z"/></svg>
        (555) 214-0387
      </li>
      <li>
        <svg viewBox="0 0 16 16"><path d="M4 0h8a1 1 0 0 1 1 1v14a1 1 0 0 1-1 1H4a1 1 0 0 1-1-1V1a1 1 0 0 1 1-1zm1 2v10h6V2zm3 11a1 1 0 1 0 0 2 1 1 0 0 0 0-2z"/></svg>
        (555) 214-0388
      </li>
      <li>
        <svg viewBox="0 0 16 16"><path d="M1 3h14v10H1zm1.5 1.2V5l5.5 4 5.5-4v-.8z"/></svg>
        info@heronloans.com
      </li>
      <li>
        <svg viewBox="0 0 16 16"><path d="M8 1a7 7 0 1 0 0 14A7 7 0 0 0 8 1zm0 1.5c.8 0 1.7 1.7 2 4H6c.3-2.3 1.2-4 2-4zM2.6 7.5h2.3c0-1.7.4-3.2 1-4.3A5.5 5.5 0 0 0 2.6 7.5zm8.5 0h2.3a5.5 5.5 0 0 0-3.3-4.3c.6 1.1 1 2.6 1 4.3zM6 8.5h4c-.2 2.6-1.1 5-2 5s-1.8-2.4-2-5zm-3.4 0a5.5 5.5 0 0 0 3.3 4.3c-.6-1.1-1-2.6-1-4.3zm8.5 0c0 1.7-.4 3.2-1 4.3a5.5 5.5 0 0 0 3.3-4.3z"/></svg>
        www.heronloans.com
      </li>
    </ul>

    <p class="address">1480 Lakeside Ave. Suite 300 Riverton, TX 75001</p>
  </section>

  <section class="card card--back" aria-label="Card back">
    <div class="wordmark">Heron Loan Partners</div>
  </section>

</main>
</body>
</html>
```